New Sports Team- Womens Football

New team in San Diego.  Looking for a website that can be updated by us after the design is established.
Pages needed:
About us
Roster
Coaches/Staff
Schedule
Online Store (This link will go out to an external vendor)
Community Partners /Sponsors
Some good team pages to take a look at:
ridgecrestcomets.com
pinehavenrangersfootball.com

Please use the logo I attempted to upload.  Looking for Flash Intro that incorporates the definition of the word "TALON" and then the logo appearing.
Use the following words:
;any sudden, strong increase, as of energy, enthusiasm, etc.
;To improve one's performance suddenly, especially in bettering one's standing in a competition.

I placed a couple more pictures.
Adding another version of the team logo. In all designs I have seen thus far, everyone has the logo very small and it appears transparent. Might help to have the jpeg version. Also added some more photos
We are approaching the deadline quickly. Just a few last notes to the designs I have been viewing. All designs that are not close to the brief will be eliminated.

```html
<!DOCTYPE html>
<html lang="en">
<head>
<meta charset="utf-8">
<title>TALON Women's Football</title>
<link href="https://fonts.googleapis.com/css2?family=Arimo:wght@400;700&display=swap" rel="stylesheet">
<style>
:root{
  --page:#0f2a5c;
  --topbar:#07080c;
  --blue:#1a8fd6;
  --blue-deep:#0b4fa8;
  --blue-light:#6cc3f0;
  --nav:#3a3a3a;
  --nav-active:#1668cf;
  --panel:#1c1c1c;
  --panel-mid:#2b2b2b;
  --row:#333;
  --side:#e9e9e9;
  --side-grey:#b9b9b9;
  --ink:#111;
  --muted:#777;
  --white:#fff;
  --footer-link:#8ea6cf;
}
*{box-sizing:border-box;margin:0;padding:0}
html,body{width:873px;height:1200px;overflow:hidden}
body{background:var(--page);font-family:"Arimo",Arial,sans-serif;position:relative;color:var(--white)}
.abs{position:absolute}
.topbar{left:0;top:0;width:873px;height:22px;background:var(--topbar);font-size:10px;display:flex;justify-content:flex-end;align-items:center;gap:9px;padding-right:100px}
.topbar b{font-weight:700}
.header{left:93px;top:37px;width:700px;height:136px;border-radius:12px;overflow:hidden;background:linear-gradient(90deg,#e9f4fb 0,#5bb5ea 18%,var(--blue) 45%,var(--blue-deep) 100%)}
.brand{left:40px;top:34px;font-size:34px;font-weight:700;color:var(--white);display:flex;align-items:center;gap:10px;letter-spacing:1px}
.brand i{display:block;width:18px;height:18px;border-radius:50%;background:var(--white)}
.call{right:10px;top:18px;font-size:18px}
.social{right:8px;top:59px;display:flex;gap:6px}
.social span{width:24px;height:24px;border-radius:5px;background:var(--white);opacity:.9}
.nav{left:0;top:87px;width:700px;height:27px;background:var(--blue-deep);display:flex;gap:3px}
.nav a{width:74px;height:27px;background:linear-gradient(#4a4a4a,#2c2c2c);color:var(--white);text-decoration:none;font-size:11px;font-weight:700;display:flex;align-items:center;justify-content:center}
.nav a.active{background:var(--nav-active);width:78px}
.header .strip{left:0;top:114px;width:700px;height:22px;background:linear-gradient(90deg,var(--white) 0,var(--white) 40%,#dfe9f5 100%);border-top:2px solid #a9c6ec}
.slider{left:91px;top:191px;width:706px;height:340px;border-radius:12px;background:var(--panel)}
.hero-photo{left:10px;top:10px;width:415px;height:242px;background:linear-gradient(#6f8b5a 0,#b93a34 45%,#7b2622 70%,#4f7d38 100%)}
.hero-caption{left:10px;top:252px;width:415px;height:77px;background:var(--panel-mid);padding:14px 20px}
.hero-caption h2{font-size:13px;font-weight:700}
.hero-caption p{font-size:8px;margin-top:14px;color:#ddd}
.play{right:20px;top:38px;width:20px;height:20px}
.thumbs{left:437px;top:10px;width:263px}
.thumb{display:flex;height:77px;margin-bottom:4px;background:var(--panel-mid)}
.thumb:first-child{border-left:4px solid var(--white)}
.thumb .txt{flex:1;padding:16px 8px 0 14px;font-size:8px;font-weight:700;line-height:11px;color:#e6e6e6}
.thumb .img{width:116px;height:77px}
.left-col{left:92px;top:540px;width:148px;height:447px;border-radius:10px 0 0 10px;overflow:hidden;background:var(--side)}
.box-title{font-size:13px;font-weight:700;color:var(--ink);padding:14px 14px 10px}
.contact{height:200px;background:var(--white)}
.form{padding:0 12px}
.form div{height:14px;border:1px solid #999;font-size:6px;color:#888;padding:2px 3px;margin-bottom:3px;background:var(--white)}
.form .msg{height:63px}
.btns{display:flex;gap:6px;justify-content:center;margin-top:7px}
.btns span{background:var(--blue-deep);font-size:8px;padding:3px 10px;border:1px solid #0a3a80}
.articles{height:247px;background:linear-gradient(var(--white),var(--side-grey))}
.article{margin:0 14px;padding:6px 0 8px;border-bottom:1px solid #999;color:var(--ink);font-size:8px;line-height:11px}
.article b{display:block;font-size:8px}
.see{color:var(--ink);font-size:8px;font-weight:700;text-decoration:underline;display:block}
.center{left:244px;top:540px;width:399px;height:600px;background:var(--panel)}
.tabs{display:flex;height:24px;font-size:10px;color:#ccc}
.tabs span{padding:7px 10px 0}
.tabs .on{background:#0d0d0d;color:var(--white);font-weight:700}
.headlines{margin:14px 12px 0;background:#111}
.headlines div{display:flex;height:26px;align-items:center;border-bottom:1px solid #2a2a2a;font-size:8px}
.headlines .date{width:80px;color:#666;text-align:center}
.headlines b{color:var(--white)}
.topics{left:0;top:200px;width:399px;height:400px;background:var(--panel-mid);padding:18px 14px 0}
.topics h3{font-size:15px;font-weight:700;margin-bottom:10px}
.topic h4{font-size:11px;line-height:13px;font-weight:700;margin-bottom:10px}
.topic .row{display:flex;gap:10px}
.topic .img{width:184px;height:118px;flex:none}
.topic p{font-size:8px;line-height:12px;color:#aaa}
.topic{border-bottom:2px solid #ccc;padding-bottom:8px;margin-bottom:12px}
.right-col{left:647px;top:540px;width:148px;height:580px;border-radius:0 10px 0 0;background:linear-gradient(var(--white),var(--side-grey));color:var(--ink);padding:0 12px}
.right-col h3{font-size:15px;font-weight:700;padding:10px 0 6px}
.news{padding-bottom:6px;border-bottom:1px solid #999;margin-bottom:8px}
.news b{font-size:8px;display:block;margin-bottom:6px}
.news .img{width:120px;height:62px;margin-bottom:10px}
.news p{font-size:8px;line-height:11px}
.footer{left:109px;top:1154px;display:flex;gap:13px;font-size:11px;color:var(--footer-link)}
.ph-red{background:linear-gradient(#c84b2c,#e37a34 50%,#3c78c0)}
.ph-grass{background:linear-gradient(#a8c6e3,#6b9b3d 60%,#456d28)}
.ph-purple{background:linear-gradient(#5a3ea0,#d7b23a 60%,#3c6d2d)}
</style>
</head>
<body>
<div class="abs topbar"><b>New User?</b><span>Register</span><span>Sign In</span><span>Help</span></div>

<header class="abs header">
  <div class="abs brand"><i></i>TALON</div>
  <div class="abs call">CALL US:555.014.2870</div>
  <div class="abs social"><span></span><span></span><span></span></div>
  <nav class="abs nav">
    <a class="active" href="#">ABOUT US</a><a href="#">ROSTER</a><a href="#">STAFF</a><a href="#">SCHEDULE</a><a href="#">ONLINE</a><a href="#">STORE</a><a href="#">COMMUNITY</a><a href="#">SPONSORS</a>
  </nav>
  <div class="abs strip"></div>
</header>

<section class="abs slider">
  <div class="abs hero-photo" role="img" aria-label="Team photo of the women's squad in red kit on a field"></div>
  <div class="abs hero-caption">
    <h2>Lorem Ipsum is simply dummy text of the printing and&nbsp; industry.</h2>
    <p>Lorem Ipsum is simply dummy text of the printing and typesetting industry.</p>
    <svg class="abs play" viewBox="0 0 20 20"><circle cx="10" cy="10" r="8.5" fill="none" stroke="#fff" stroke-width="1.5"/><path d="M8 6l6 4-6 4z" fill="#fff"/></svg>
  </div>
  <div class="abs thumbs">
    <div class="thumb"><div class="txt">SEP 10,2010<br>It is a long established fact that a reader will be distracted by the&nbsp; .</div><div class="img ph-grass" role="img" aria-label="Players contesting the ball in a match"></div></div>
    <div class="thumb"><div class="txt">SEP 10,2010<br>It is a long established fact that a reader will be distracted by the&nbsp; .</div><div class="img ph-purple" role="img" aria-label="Two players in purple and gold kit"></div></div>
    <div class="thumb"><div class="txt">SEP 10,2010<br>It is a long established fact that a reader will be distracted by the&nbsp; .</div><div class="img ph-red" role="img" aria-label="Young player wearing a medal"></div></div>
    <div class="thumb"><div class="txt">SEP 10,2010<br>It is a long established fact that a reader will be distracted by the&nbsp; .</div><div class="img ph-grass" role="img" aria-label="Young player kneeling with a ball"></div></div>
  </div>
</section>

<aside class="abs left-col">
  <div class="contact">
    <div class="box-title">CONTACT US</div>
    <div class="form"><div>Name:</div><div>Email:</div><div>Phone:</div><div class="msg">Message:</div></div>
    <div class="btns"><span>Sumit</span><span>Clear</span></div>
  </div>
  <div class="articles">
    <div class="box-title">LATEST ARTICLES</div>
    <div class="article"><b>SEP 10,2010</b>It is a long established fact that a reader will be distracted by the</div>
    <div class="article"><b>SEP 10,2010</b>It is a long established fact that a reader will be distracted by the</div>
    <div class="article"><b>SEP 10,2010</b>It is a long established fact that a reader will be distracted by the</div>
    <a class="see" style="margin:12px 14px 0">See all</a>
  </div>
</aside>

<main class="abs center">
  <div class="tabs"><span class="on">HEADLINES</span><span>FULL SCHEDULE</span><span>APPEARANCES</span></div>
  <div class="headlines">
    <div><span class="date">SEP 10,2010</span><b>Lorem Ipsum is simply dummy text of the printing and&nbsp; industry.</b></div>
    <div><span class="date">SEP 10,2010</span><b>Lorem Ipsum is simply dummy text of the printing and&nbsp; industry.</b></div>
    <div><span class="date">SEP 10,2010</span><b>Lorem Ipsum is simply dummy text of the printing and&nbsp; industry.</b></div>
    <div><span class="date">SEP 10,2010</span><b>Lorem Ipsum is simply dummy text of the printing and&nbsp; industry.</b></div>
    <div><span class="date">SEP 10,2010</span><b>Lorem Ipsum is simply dummy text of the printing and&nbsp; industry.</b></div>
  </div>
  <section class="abs topics">
    <h3>LATEST TOPICS</h3>
    <article class="topic">
      <h4>Lorem Ipsum is simply dummy text of the printing<br>and typesetting industry.</h4>
      <div class="row"><div class="img ph-grass" role="img" aria-label="Two young players competing for the ball"></div>
      <p>Lorem Ipsum is simply dummy text of the printing and typesetting industry. Lorem Ipsum has been the industry's standard dummy text ever since the 1500s, Ipsum has been the iLorem Ipsum is simply dummy text of the printing and typesetting industry. Lorem Ipsum has been the industry's standard dummy text ever since</p></div>
    </article>
    <article class="topic">
      <h4>Lorem Ipsum is simply dummy text of the printing<br>and typesetting industry.</h4>
      <div class="row"><div class="img ph-red" role="img" aria-label="Young player in orange kit wearing a medal"></div>
      <p>Lorem Ipsum is simply dummy text of the printing and typesetting industry. Lorem Ipsum has been the industry's standard dummy text ever since the 1500s, Ipsum has been the iLorem Ipsum is simply dummy text of the printing and typesetting industry. Lorem Ipsum has been the industry's standard dummy text ever since</p></div>
    </article>
  </section>
</main>

<aside class="abs right-col">
  <h3>LATEST NEWS</h3>
  <div class="news"><b>SEP 10,2010</b><div class="img ph-grass" role="img" aria-label="Young player holding a ball"></div><p>It is a long established fact that a reader will be distracted by the</p></div>
  <div class="news"><b>SEP 10,2010</b><div class="img ph-red" role="img" aria-label="Young player wearing a medal"></div><p>It is a long established fact that a reader will be distracted by the</p></div>
  <div class="news"><b>SEP 10,2010</b><div class="img ph-red" role="img" aria-label="Young player wearing a medal"></div><p>It is a long established fact that a reader will be distracted by the</p></div>
  <div class="news" style="border:0"><b>SEP 10,2010</b><div class="img ph-red" role="img" aria-label="Young player wearing a medal"></div><p>It is a long established fact that a reader will be distracted by the</p></div>
  <a class="see" style="text-align:right">See all</a>
</aside>

<footer class="abs footer"><span>ABOUT US</span><span>ROSTER</span><span>STAFF</span><span>SCHEDULE</span><span>ONLINE</span><span>STORE</span><span>COMMUNITY</span><span>SPONSORS</span></footer>
</body>
</html>
```